Responsive Wordpress Site Design - Veterans Job Site

I need a re-design of my web page, www.pinnorahires.com. I want it to be Responsive so it looks great on mobile. I am a job recruiter for military veterans in the U.S. Here is a sample re-design site that a different developer just finished for me: http://pinnorahires.com/test/ I fired him because I got frustrated with his design abilities. But, this site is the general idea of what I want. I want the colors to be red, white and blue. I like a lot of white space so, big type, and video/pictures so it's easy on the eyes. I like this page: http://quillmarsporting.com/ . I do a lot with videos (that's how I present my veterans to companies, testimonials, job tips) so I would like to have a lot of video on the page. I want the home page to be one long scrolling page so it is easy to navigate on mobile and I can load it with keywords for SEO. I want the page to have a patriotic and powerful feel.

Target Market(s)

I have two audiences: Veterans looking for jobs and Companies looking to hire jobs. Right now I focus on the state of Connecticut, but next month I'm expanding to Massachusetts and I have plans to expand nationwide.

Industry/Entity Type

Marketing

Font styles to use
Sans Serif

Colors
ec1f27
0455a3
ffffff

Requirements
Must have
• Lots of Vidstream videos...overviews of how the company works (I'll create this videos later, just use a placeholder for now), testimonials, job tips
• Social media feeds for Friendwall and Chirpline
• Big pictures
• Top section big and clear for Veterans to "Register Free"...this will bounce to my registration page...the most important goal of the site.
• Big and clear way for Companies to complete a form to request more information.
• Highlight videos of testimonials...the success stories
• Big headlines and text so the page is easy on the eyes and easy to read on a mobile phone.
• Lots of white space
• A professional look...want viewers to see the company as a strong
• I need the ability to edit the page when you're done....to add forms, additional pages, etc.
Nice to have
• see must haves
Should not have
• see must haves

```html
<!DOCTYPE html>
<html lang="en">
<head>
<meta charset="utf-8">
<title>Pinnora Hires – Great Jobs for Veterans</title>
<link href="https://fonts.googleapis.com/css2?family=Open+Sans:ital,wght@0,400;0,600;0,700;0,800;1,400;1,600&display=swap" rel="stylesheet">
<style>
:root{
  --red:#ec1f27;
  --blue:#0455a3;
  --navy:#0b3f86;
  --white:#ffffff;
  --btn-blue:#1877b8;
  --text:#555;
  --muted:#9a9a9a;
  --rule:#e8e8e8;
  --band:#f4f4f4;
  --foot:#333333;
  --foot-dark:#2a2a2a;
  --foot-text:#cfcfcf;
  --link-blue:#1a8fd0;
}
*{box-sizing:border-box;margin:0;padding:0}
html,body{width:1200px;height:2862px;overflow:hidden}
body{font-family:"Open Sans",Arial,sans-serif;background:var(--white);color:var(--text);position:relative}
.abs{position:absolute}

/* header */
.site-header{position:absolute;left:0;top:0;width:1200px;height:122px;background:var(--white)}
.brand{position:absolute;left:100px;top:24px;display:flex;align-items:center;gap:14px}
.brand-mark{width:62px;height:62px;background:var(--blue)}
.brand-name{font-weight:800;font-size:34px;color:var(--blue);letter-spacing:.5px;line-height:1}
.brand-tag{font-size:11px;font-style:italic;font-weight:600;color:var(--blue);margin-top:6px}
.btn-register{position:absolute;left:916px;top:38px;width:182px;height:48px;background:var(--red);color:var(--white);font-weight:700;font-size:16px;display:flex;align-items:center;justify-content:center;border-radius:3px;letter-spacing:.5px}

/* nav */
.main-nav{position:absolute;left:0;top:122px;width:1200px;height:59px;background:var(--blue);border-bottom:3px solid #033f7a}
.main-nav ul{list-style:none;display:flex;position:absolute;left:100px;top:0;height:56px}
.main-nav li{color:var(--white);font-weight:700;font-size:14px;text-transform:uppercase;display:flex;align-items:center;padding:0 23px;height:56px}
.main-nav li.active{background:var(--red);padding:0 38px}

/* hero */
.hero{position:absolute;left:0;top:181px;width:1200px;height:552px;background:radial-gradient(ellipse at 50% 40%,#ffffff 0%,#f2f2f2 55%,#e6e6e6 100%)}
.hero-title{position:absolute;top:62px;width:100%;text-align:center;font-weight:800;font-size:38px;line-height:46px;color:var(--navy);text-transform:uppercase}
.hero-title .red{color:var(--red)}
.hero-people{position:absolute;left:200px;top:220px;width:775px;height:332px;background:linear-gradient(90deg,#cfd3d6 0%,#3c4047 20%,#d9dde2 42%,#2b2f36 55%,#8d8a6a 72%,#2b2e33 88%,#dcdfe2 100%);border-radius:120px 120px 0 0}
.hero-arrow{position:absolute;top:245px}

/* section headings */
.section-title{position:absolute;width:100%;text-align:center;font-weight:800;font-size:38px;text-transform:uppercase;color:var(--blue)}
.section-title .red,.col-title .red{color:var(--red)}
.lede{position:absolute;width:100%;text-align:center;font-size:12px;line-height:22px;color:var(--muted)}
.lede-blue{position:absolute;width:100%;text-align:center;font-size:15px;line-height:24px;color:var(--btn-blue);font-style:italic;font-weight:600}
.btn-apply{position:absolute;left:527px;top:967px;width:147px;height:48px;background:var(--btn-blue);color:var(--white);font-weight:700;font-size:16px;display:flex;align-items:center;justify-content:center;border-radius:3px}
.rule{position:absolute;left:100px;width:998px;height:1px;background:var(--rule)}

/* video cards */
.video{position:absolute;overflow:hidden}
.video .frame{position:absolute;left:0;top:0;right:0;bottom:26px}
.video .play{position:absolute;left:50%;top:45%;transform:translate(-50%,-50%);width:46px;height:46px;border-radius:50%;background:rgba(20,20,20,.65)}
.video .play::after{content:"";position:absolute;left:18px;top:14px;border-left:14px solid #fff;border-top:9px solid transparent;border-bottom:9px solid transparent}
.video .controls{position:absolute;left:0;right:0;bottom:0;height:26px;background:#1b1b1b;color:#ddd;font-size:9px;display:flex;align-items:center;padding:0 10px;gap:14px}
.video .controls .vendor{margin-left:auto;font-weight:700;color:#fff}
.video.big .controls{height:42px;font-size:12px}
.video.big .frame{bottom:42px}
.video.big .play{width:74px;height:74px}
.video.big .play::after{left:29px;top:23px;border-left:22px solid #fff;border-top:14px solid transparent;border-bottom:14px solid transparent}
.progress{position:absolute;left:0;right:0;height:3px;background:#555}

/* testimonial */
.col-title{position:absolute;font-weight:800;font-size:36px;text-transform:uppercase;color:var(--blue)}
.quote-mark{position:absolute;left:652px;top:1690px;font-size:60px;line-height:50px;font-weight:800;color:var(--red)}
.quote{position:absolute;left:706px;top:1688px;width:392px;font-size:13.5px;line-height:24px;font-style:italic;color:var(--text)}
.quote-name{position:absolute;left:652px;top:1906px;font-weight:700;font-size:15px;color:var(--blue)}
.dots{position:absolute;left:1048px;top:1914px;display:flex;gap:4px}
.dots span{width:8px;height:8px;border-radius:50%;background:#ccc}
.dots span.on{background:var(--blue)}

/* feeds */
.feeds-band{position:absolute;left:0;top:1993px;width:1200px;height:545px;background:var(--band);border-top:1px solid #e5e5e5}
.feed-box{position:absolute;top:2125px;width:473px;height:335px;background:var(--white);border:1px solid #e1e1e1;box-shadow:0 1px 4px rgba(0,0,0,.08)}
.feed-head{height:40px;display:flex;align-items:center;padding:0 16px;font-size:13px;color:var(--blue);border-bottom:1px solid #eee}
.feed-head .icons{margin-left:auto;display:flex;gap:6px}
.feed-head .icons i{width:11px;height:11px;border-radius:50%;background:#c8c8c8;display:block}
.feed-item{display:flex;gap:18px;padding:16px 16px 0;height:95px;border-bottom:1px solid #eee}
.feed-item:last-child{border-bottom:none}
.avatar{width:62px;height:54px;flex:none}
.tweet-dot{width:22px;height:22px;border-radius:50%;background:var(--link-blue);flex:none;margin:6px 10px 0 4px}
.feed-text{font-size:13px;line-height:21px;color:#444}
.feed-meta{font-size:9.5px;color:var(--link-blue);margin-top:4px}

/* footer */
.site-footer{position:absolute;left:0;top:2538px;width:1200px;height:262px;background:var(--foot)}
.foot-col{position:absolute;top:2578px}
.foot-col h4{font-weight:800;font-size:20px;color:var(--white);text-transform:uppercase;margin-bottom:22px}
.foot-col ul{list-style:none}
.foot-col li{font-size:12px;color:var(--foot-text);height:35px;line-height:17px;border-bottom:1px solid #3f3f3f;margin-bottom:0;padding-top:4px;width:140px}
.foot-col.start li{width:150px;padding-top:8px;height:44px}
.news-input{position:absolute;left:887px;top:2573px;width:211px;height:40px;background:var(--white);font-size:11px;color:#888;padding:12px 10px}
.btn-signup{position:absolute;left:980px;top:2640px;width:118px;height:43px;background:var(--red);color:var(--white);font-weight:700;font-size:16px;display:flex;align-items:center;justify-content:center}
.bottom-bar{position:absolute;left:0;top:2800px;width:1200px;height:62px;background:var(--foot-dark)}
.social{position:absolute;left:95px;top:0;display:flex}
.social span{width:75px;height:62px;display:flex;align-items:center;justify-content:center}
.social span i{width:12px;height:12px;border-radius:50%;background:#ddd;display:block}
.social span.first{background:var(--blue)}
.social span.first i{background:#fff}
.copyright{position:absolute;right:102px;top:23px;font-size:12px;color:var(--foot-text)}
</style>
</head>
<body>

<header class="site-header">
  <div class="brand">
    <div class="brand-mark"></div>
    <div>
      <div class="brand-name">PINNORA HIRES</div>
      <div class="brand-tag">Great Employees For Companies...Great Jobs For Veterans</div>
    </div>
  </div>
  <div class="btn-register">REGISTER FREE</div>
</header>

<nav class="main-nav">
  <ul>
    <li class="active">Home</li>
    <li>About Us</li>
    <li>Job Openings</li>
    <li>Apply Now</li>
    <li>Interested Employers</li>
    <li>Testimonials</li>
    <li>Blog</li>
  </ul>
</nav>

<section class="hero">
  <h1 class="hero-title">Great Employees for Companies...<br><span class="red">Great Jobs</span> for Veterans</h1>
  <div class="hero-people" role="img" aria-label="Three smiling veterans, one in uniform and two in civilian work clothes"></div>
  <svg class="hero-arrow" style="left:22px" width="36" height="64" viewBox="0 0 36 64"><polyline points="32,2 4,32 32,62" fill="none" stroke="#c9c9c9" stroke-width="2"/></svg>
  <svg class="hero-arrow" style="left:1142px" width="36" height="64" viewBox="0 0 36 64"><polyline points="4,2 32,32 4,62" fill="none" stroke="#c9c9c9" stroke-width="2"/></svg>
</section>

<section class="welcome">
  <h2 class="section-title" style="top:776px"><span class="red">Welcome to</span> Pinnora Hires</h2>
  <p class="lede-blue" style="top:836px">We help Connecticut military veterans land great full-time jobs. We have dozens of immediate openings in<br>customer service, manufacturing, sales, construction, field service, healthcare, accounting, and IT.</p>
  <p class="lede" style="top:898px">But I must explain to you how all this mistaken idea of denouncing pleasure and praising pain was born and I will give you a co<br>and expound the actual teachings of the great explorer of the truth, the master-builder of human happincts, dislikes,</p>
  <div class="btn-apply">APPLY NOW</div>
</section>

<div class="rule" style="top:1048px"></div>

<section class="company-works">
  <h2 class="section-title" style="top:1092px"><span class="red">Company</span> Works</h2>
  <p class="lede" style="top:1158px">But I must explain to you how all this mistaken idea of denouncing pleasure and praising pain was born and I will give you a co<br>and expound the actual teachings of the great explorer of the truth, the master-builder of human happincts, dislikes,</p>

  <div class="video" style="left:100px;top:1242px;width:317px;height:255px">
    <div class="frame" role="img" aria-label="Video still of colleagues talking at a desk" style="background:linear-gradient(135deg,#cfd8e0,#8a8f95 50%,#e6e8ea)"></div>
    <div class="play"></div>
    <div class="controls"><span>▶</span><span>00:00 / 1:20</span><span class="vendor">Vidstream</span></div>
  </div>
  <div class="video" style="left:441px;top:1242px;width:317px;height:255px">
    <div class="frame" role="img" aria-label="Video still of a smiling group of professionals" style="background:linear-gradient(135deg,#d8dee6,#7d8794 50%,#c3ccd6)"></div>
    <div class="play"></div>
    <div class="controls"><span>▶</span><span>00:00 / 1:20</span><span class="vendor">Vidstream</span></div>
  </div>
  <div class="video" style="left:780px;top:1242px;width:318px;height:255px">
    <div class="frame" role="img" aria-label="Video still of a team working at computers" style="background:linear-gradient(135deg,#e5e7ea,#8e949a 50%,#bfc6cf)"></div>
    <div class="play"></div>
    <div class="controls"><span>▶</span><span>00:00 / 1:20</span><span class="vendor">Vidstream</span></div>
  </div>
  <svg class="abs" style="left:50px;top:1346px" width="24" height="46" viewBox="0 0 24 46"><polyline points="22,2 3,23 22,44" fill="none" stroke="#c9c9c9" stroke-width="2"/></svg>
  <svg class="abs" style="left:1126px;top:1346px" width="24" height="46" viewBox="0 0 24 46"><polyline points="2,2 21,23 2,44" fill="none" stroke="#c9c9c9" stroke-width="2"/></svg>
</section>

<div class="rule" style="top:1563px"></div>

<section class="testimonials">
  <div class="video big" style="left:100px;top:1625px;width:527px;height:308px">
    <div class="frame" role="img" aria-label="Video still of a businessman in an office" style="background:linear-gradient(90deg,#a9c3d8,#d7e3ec 45%,#c9b8a7 75%,#eef2f5)"></div>
    <div class="play"></div>
    <div class="progress" style="bottom:42px"></div>
    <div class="controls"><span>▶</span><span>🔈</span><span>00:00 / 2:25</span><span class="vendor">Vidstream</span></div>
  </div>
  <h2 class="col-title" style="left:652px;top:1614px"><span class="red">Client</span> Testimonials</h2>
  <div class="quote-mark">“</div>
  <p class="quote">But I must explain to you how all this mistaken idea of denounc pleasure and praising pain was born and I will give you a coand expound the actual teachings of the gBut I must explain to you how all this mistaken idea of denouncing pleasure and praising pain was born and I will give you a coand expound the actual teachings of the great explorer of the truth, the master-builder of human happincts, dislikes, reat explorer of the truth, the master-builder of human happincts, dislikeof the truth, the master-builder of humans”</p>
  <div class="quote-name">Dale Morrow , city Name</div>
  <div class="dots"><span></span><span></span><span class="on"></span><span></span></div>
</section>

<section class="feeds-band">
  <h2 class="col-title" style="left:100px;top:55px"><span class="red">Friendwall</span> Feeds</h2>
  <h2 class="col-title" style="left:632px;top:55px"><span class="red">Chirpline</span> Feeds</h2>
</section>

<div class="feed-box" style="left:100px">
  <div class="feed-head">Likes on Friendwall<span class="icons"><i></i><i></i><i></i></span></div>
  <div class="feed-item">
    <div class="avatar" style="background:var(--blue)"></div>
    <div><div class="feed-text">Laudantium, totam rem aperiam, eaque ipsa quae ab illo<br>ntore veritatis et quasi architecto beatae vitae dicta...</div><div class="feed-meta">3 minutes ago &nbsp; / &nbsp; 0 comments</div></div>
  </div>
  <div class="feed-item">
    <div class="avatar" role="img" aria-label="Profile photo" style="background:linear-gradient(135deg,#d9c1a6,#8c6f55)"></div>
    <div><div class="feed-text">Laudantium, totam rem aperiam, eaque ipsa quae ab illo<br>ntore veritatis et quasi architecto beatae vitae dicta...</div><div class="feed-meta">3 minutes ago &nbsp; / &nbsp; 0 comments</div></div>
  </div>
  <div class="feed-item">
    <div class="avatar" role="img" aria-label="Profile photo" style="background:linear-gradient(135deg,#a7a07e,#5d5a44)"></div>
    <div><div class="feed-text">Laudantium, totam rem aperiam, eaque ipsa quae ab illo<br>ntore veritatis et quasi architecto beatae vitae dicta...</div><div class="feed-meta">3 minutes ago &nbsp; / &nbsp; 0 comments</div></div>
  </div>
</div>

<div class="feed-box" style="left:625px;height:300px">
  <div class="feed-head" style="color:var(--link-blue)">Latest Chirpline<span class="icons"><i></i></span></div>
  <div class="feed-item" style="height:86px">
    <div class="tweet-dot"></div>
    <div><div class="feed-text">Laudantium, totam rem aperiam, eaque ipsa quae ab illo<br>ntore veritatis et quasi architecto beatae vitae dicta...</div><div class="feed-meta">3 minutes ago &nbsp; / &nbsp; 0 comments</div></div>
  </div>
  <div class="feed-item" style="height:86px">
    <div class="tweet-dot"></div>
    <div><div class="feed-text">Laudantium, totam rem aperiam, eaque ipsa quae ab illo<br>ntore veritatis et quasi architecto beatae vitae dicta...</div><div class="feed-meta">3 minutes ago &nbsp; / &nbsp; 0 comments</div></div>
  </div>
  <div class="feed-item" style="height:86px">
    <div class="tweet-dot"></div>
    <div><div class="feed-text">Laudantium, totam rem aperiam, eaque ipsa quae ab illo<br>ntore veritatis et quasi architecto beatae vitae dicta...</div><div class="feed-meta">3 minutes ago &nbsp; / &nbsp; 0 comments</div></div>
  </div>
</div>

<footer class="site-footer"></footer>
<div class="foot-col" style="left:100px">
  <h4>Choose</h4>
  <ul><li>Home</li><li>Register Free</li><li>Testimonials</li><li>Hire A Veteran</li><li>About Us</li></ul>
</div>
<div class="foot-col" style="left:353px">
  <h4>Get Support</h4>
  <ul><li>Refer a Buddy</li><li>Supporters</li><li>FAQ</li><li>Job Tips</li></ul>
</div>
<div class="foot-col start" style="left:647px">
  <h4>Start</h4>
  <ul><li>Conse ctetur adipisic</li><li>Elit sed do eiusmod</li><li>Incididunt ut labo</li><li>Et dolore magna</li></ul>
</div>
<div class="foot-col" style="left:895px">
  <h4>Newsletter</h4>
</div>
<div class="news-input" style="top:2611px">Email address:</div>
<div class="btn-signup" style="top:2670px">SIGN UP</div>

<div class="bottom-bar">
  <div class="social"><span class="first"><i></i></span><span><i></i></span><span><i></i></span><span><i></i></span><span><i></i></span><span><i></i></span></div>
  <div class="copyright">© 2015 All Rights Reserved - PinnoraHires</div>
</div>

</body>
</html>
```